Bright Harbor Web Design & Marketing

Will award a 2nd place prize of $100.00 if someone can come up with a logo to match this design!
Updates

Okay, I'm really looking to see some better designs here. What do you think will bring the best designs out? Please remember with all future submissions I'm looking for a cartoon style / illustrator style website. I'm not sure what the technical term is for it, so I uploaded some images in the brief.

Target Market(s)

Small Business Owners

Industry/Entity Type

Marketing

Logo Text

BrightHarbor.com

Number of Pages Required

1 page

Colors

Designer to choose colors to be used in the design.

Requirements
Must have
• Logo should say BrightHarbor.com I would like more than just a text logo. I want some sort of cool custom graphic / icon with it that will look nice on shirts/hats/etc

```html
<!DOCTYPE html>
<html lang="en">
<head>
<meta charset="utf-8">
<title>Bright Harbor Web Design</title>
<link href="https://fonts.googleapis.com/css2?family=Montserrat:wght@500;600;700;800&family=Questrial&display=swap" rel="stylesheet">
<style>
:root{
  --navy:#221a78;
  --navy-dark:#16104f;
  --ink:#2b2b33;
  --muted:#6b6b75;
  --line:#dcdce2;
  --soft:#eeeef1;
  --white:#ffffff;
  --star:#f2b01e;
}
*{box-sizing:border-box;margin:0;padding:0}
html,body{width:1200px;height:4380px;overflow:hidden}
body{font-family:"Questrial",sans-serif;color:var(--ink);background:var(--white);font-size:14px}
h1,h2,h3,h4,.nav,.btn{font-family:"Montserrat",sans-serif}
.section-title{font-size:26px;font-weight:600;text-align:center;letter-spacing:.5px;color:#333}
.section-title b{color:var(--navy);font-weight:800}
.btn{display:inline-block;background:var(--navy);color:var(--white);font-weight:700;font-size:12px;border-radius:18px;padding:9px 22px;letter-spacing:.5px}

/* header */
.site-header{height:85px;display:flex;align-items:center;justify-content:space-between;padding:0 140px}
.brand{display:flex;align-items:center;gap:12px}
.brand-square{width:46px;height:46px;background:var(--navy);border-radius:6px}
.brand-name{font-family:"Montserrat",sans-serif;font-weight:800;font-size:19px;color:var(--navy);line-height:1.05}
.brand-name small{display:block;font-weight:600;font-size:14px;letter-spacing:.5px;color:#333}
.header-contact{display:flex;align-items:center;gap:28px}
.phone{display:flex;align-items:center;gap:10px;font-size:17px;color:#333}
.nav{height:35px;background:#6a6a70;display:flex;padding:0 140px}
.nav a{color:var(--white);font-size:12px;font-weight:700;flex:1;text-align:center;line-height:35px;text-decoration:none}
.nav a.active{background:var(--navy);flex:0 0 120px}

/* hero */
.hero{height:470px;background:linear-gradient(90deg,#eceef2 0%,#f3f4f7 40%,#e3e7ee 100%);position:relative;overflow:hidden}
.hero h1{position:absolute;left:145px;top:168px;font-size:25px;line-height:1.32;font-weight:700;color:#222;width:400px;z-index:2}
.hero-visual{position:absolute;left:440px;right:0;top:0;bottom:0;
  background:
    radial-gradient(ellipse 30% 38% at 30% 42%,#2d3444 0%,rgba(45,52,68,.85) 50%,rgba(45,52,68,0) 100%),
    radial-gradient(ellipse 26% 34% at 62% 36%,#3a4256 0%,rgba(58,66,86,.8) 55%,rgba(58,66,86,0) 100%),
    radial-gradient(ellipse 24% 40% at 88% 48%,#d9dde4 0%,rgba(150,160,175,.7) 55%,rgba(150,160,175,0) 100%),
    radial-gradient(ellipse 20% 22% at 45% 70%,#2a8fd0 0%,rgba(42,143,208,0) 100%),
    linear-gradient(90deg,rgba(236,238,242,1) 0%,rgba(236,238,242,0) 25%);}
.dots{position:absolute;left:145px;top:332px;display:flex;gap:6px}
.dots i{width:10px;height:10px;border-radius:50%;background:#555}
.dots i+i{background:#999}

/* about */
.about{height:270px;padding-top:64px;text-align:center}
.about p{width:920px;margin:14px auto 0;font-size:13px;line-height:1.6;color:#444}
.about p+p{margin-top:10px}

/* services */
.services{height:665px;background:var(--soft);padding-top:60px}
.service-grid{display:grid;grid-template-columns:repeat(3,290px);gap:24px 23px;margin:42px auto 0;width:916px}
.service-card{background:var(--white);height:145px;padding:22px 20px;display:flex;gap:16px;box-shadow:0 2px 6px rgba(0,0,0,.1)}
.service-card svg{flex:0 0 38px}
.service-card h3{font-size:14px;font-weight:600;color:#222;line-height:1.25}
.service-card p{font-size:11px;color:var(--muted);line-height:1.45;margin-top:10px}

/* cta */
.cta{height:265px;background:radial-gradient(ellipse 40% 70% at 85% 60%,#4a4d58,rgba(74,77,88,0)),radial-gradient(ellipse 35% 60% at 12% 40%,#3a3c46,rgba(58,60,70,0)),linear-gradient(90deg,#121218,#2c2e38 50%,#15151b);text-align:center;padding-top:78px;color:var(--white)}
.cta p{width:760px;margin:0 auto 22px;font-size:15px;line-height:1.6}

/* different */
.different{height:360px;padding-top:52px}
.features{display:flex;justify-content:center;gap:40px;margin-top:40px}
.feature{width:190px;text-align:center}
.feature-icon{width:80px;height:80px;border-radius:50%;border:3px solid var(--navy);margin:0 auto 14px;display:flex;align-items:center;justify-content:center}
.feature h4{font-size:13px;font-weight:600;color:#222;line-height:1.3}
.feature p{font-size:10.5px;color:var(--muted);line-height:1.45;margin-top:6px}

/* portfolio */
.portfolio{height:580px;background:var(--soft);padding-top:64px}
.filters{display:flex;justify-content:center;gap:12px;margin-top:20px}
.filters span{font-size:11px;padding:6px 16px;background:var(--white);border:1px solid var(--line);color:#444}
.filters span.on{background:var(--navy);color:var(--white)}
.work-grid{display:grid;grid-template-columns:repeat(4,212px);gap:22px;width:914px;margin:36px auto 0}
.work{height:155px;box-shadow:0 2px 5px rgba(0,0,0,.15)}

/* team */
.team{height:600px;padding-top:70px;position:relative}
.team-row{display:flex;justify-content:center;gap:20px;margin-top:35px}
.member{width:155px;height:205px;background:#f4f4f6;border:1px solid var(--line);border-radius:6px;text-align:center;padding-top:14px;position:relative;overflow:hidden}
.photo{border-radius:50%;background:radial-gradient(circle at 50% 38%,#e8d3c2 0 22%,rgba(232,211,194,0) 23%),radial-gradient(ellipse 60% 45% at 50% 100%,#2f3a55 0 70%,rgba(47,58,85,0) 71%),linear-gradient(#eef1f5,#c9d0da)}
.member .photo{width:90px;height:90px;margin:0 auto;border:3px solid var(--white);box-shadow:0 0 0 1px var(--line)}
.member h4{font-size:14px;font-weight:600;margin-top:10px}
.member p{font-size:11px;color:var(--muted)}
.member .social{position:absolute;left:0;right:0;bottom:0;height:36px;background:#5a5a60;display:flex;justify-content:center;align-items:center;gap:6px}
.member.active .social{background:var(--navy)}
.member .social i{width:20px;height:20px;border-radius:50%;border:1.5px solid var(--white)}
.arrow{position:absolute;top:290px;width:22px;height:22px;border-radius:50%;border:1px solid var(--line)}
.team-bio{width:920px;margin:28px auto 0;padding:22px 28px;box-shadow:0 1px 6px rgba(0,0,0,.15);font-size:12.5px;line-height:1.55;color:#333}
.team-bio p+p{margin-top:14px}

/* reviews */
.reviews{height:420px;background:var(--soft);padding-top:75px}
.review-row{display:flex;justify-content:center;gap:40px;margin-top:34px}
.review{width:440px;display:flex;gap:16px}
.review-person{width:90px;text-align:center}
.review-person .photo{width:80px;height:80px;margin:0 auto}
.review-person h4{font-size:12px;font-weight:700;color:var(--navy);margin-top:6px}
.stars{color:var(--star);font-size:11px}
.review p{font-size:11px;font-style:italic;color:#555;line-height:1.55;flex:1}
.slider-line{width:480px;height:2px;background:#bbb;margin:40px auto 0;position:relative}
.slider-line i{position:absolute;left:50%;top:-9px;width:20px;height:20px;margin-left:-10px;border-radius:50%;background:var(--navy)}

/* clients */
.clients{height:270px;padding-top:70px;position:relative}
.client-row{display:flex;justify-content:center;gap:14px;margin-top:38px}
.client{width:132px;height:78px;border:1px solid var(--line);display:flex;align-items:center;justify-content:center;gap:6px;font-size:17px;color:#333}
.client i{width:12px;height:12px;background:#333;border-radius:50%}
.chev{position:absolute;top:175px;font-size:26px;color:#555}

/* newsletter + footer */
.newsletter{height:48px;background:var(--navy);display:flex;align-items:center;padding:0 140px;gap:14px;color:var(--white)}
.newsletter h3{font-size:17px;font-weight:700;letter-spacing:.5px;flex:1}
.newsletter .field{width:390px;height:28px;background:var(--white);display:flex;justify-content:space-between;align-items:center;padding-left:10px;color:#999;font-size:10px}
.newsletter .field span{background:#666;color:var(--white);font-family:"Montserrat",sans-serif;font-size:11px;font-weight:700;padding:0 16px;line-height:28px}
.site-footer{height:282px;background:radial-gradient(ellipse 35% 70% at 85% 70%,#3d3f48,rgba(61,63,72,0)),linear-gradient(180deg,#2e2f36,#1f2026);display:flex;padding:26px 140px 0;gap:60px;color:#ddd}
.site-footer h4{font-size:13px;font-weight:700;color:var(--white);margin-bottom:14px}
.site-footer li{list-style:none;font-size:12px;line-height:2}
.contact-line{display:flex;gap:8px;font-size:12px;margin-bottom:12px;align-items:flex-start}
.inquiry .input{width:190px;height:26px;background:var(--white);margin-bottom:8px;color:#888;font-size:10px;padding:6px}
.inquiry .msg{height:40px}
.btn-small{display:inline-block;background:var(--navy);color:var(--white);font-family:"Montserrat",sans-serif;font-weight:700;font-size:10px;padding:5px 12px}
.footer-brand{margin-left:auto;padding-top:50px;text-align:center}
.footer-brand .brand-name{color:var(--white);font-size:22px;margin-bottom:16px;text-align:center}
.footer-brand .brand-name small{color:#ccc}
.footer-social{display:flex;gap:6px;justify-content:center}
.footer-social i{width:20px;height:20px;border-radius:50%;background:#3b5fa8}
.copyright{height:30px;background:#131318;color:#bbb;text-align:center;font-size:11px;line-height:30px}
</style>
</head>
<body>

<header class="site-header">
  <div class="brand"><span class="brand-square"></span><span class="brand-name">BRIGHT HARBOR<small>WEB DESIGN</small></span></div>
  <div class="header-contact">
    <div class="phone">
      <svg width="26" height="26" viewBox="0 0 26 26"><circle cx="13" cy="13" r="12" fill="none" stroke="#333" stroke-width="1.5"/><path d="M9 7l3 3-2 2c1 2 2 3 4 4l2-2 3 3-2 2c-5 0-10-5-10-10z" fill="#333"/></svg>
      123.456.7890
    </div>
    <span class="btn">CONTACT US NOW</span>
  </div>
</header>
<nav class="nav"><a class="active">HOME</a><a>SERVICES &amp; PRICING</a><a>OUR TEAM</a><a>CLIENTS/PORTFOLIO</a><a>CONTACT US</a></nav>

<section class="hero">
  <div class="hero-visual" role="img" aria-label="Group of computer screens and tablets showing sample websites"></div>
  <h1>The Design &amp; Marketing Team That Always Puts Trust &amp; Loyalty Before Profits</h1>
  <div class="dots"><i></i><i></i><i></i></div>
</section>

<section class="about">
  <h2 class="section-title">ABOUT <b>BRIGHT HARBOR</b> WEB DESIGN</h2>
  <p>We believe that honesty and integrity come before personal profits. We are a family owned and operated company. Our parents raised us to take care of each other and that's exactly what we've done. We treat each of our clients with the same loyalty and respect that we give each other.</p>
  <p>We are not looking to have hundreds and hundreds of clients. We are looking to expand our family with a handful of like-minded individuals. Companies who take pride in their work and their customers. We want to build mutually beneficial, lucrative, and long term partnerships.</p>
</section>

<section class="services">
  <h2 class="section-title">OUR <b>SERVICES</b></h2>
  <div class="service-grid">
    <div class="service-card"><svg width="38" height="38" viewBox="0 0 38 38"><rect x="3" y="6" width="32" height="22" rx="2" fill="none" stroke="#221a78" stroke-width="2.5"/><path d="M13 33h12M19 28v5" stroke="#221a78" stroke-width="2.5"/></svg><div><h3>Website Design<br>&amp; Management</h3><p>Lorem ipsum dolor sit amet, consectetuer adipiscing elit, sed diam nonummy nibh euismod tincidunt ut laoreet</p></div></div>
    <div class="service-card"><svg width="38" height="38" viewBox="0 0 38 38"><path d="M6 32l6-2 20-20-4-4-20 20z" fill="none" stroke="#221a78" stroke-width="2.5"/></svg><div><h3>Logo Design<br>&amp; Branding Materials</h3><p>Lorem ipsum dolor sit amet, consectetuer adipiscing elit, sed diam nonummy nibh euismod tincidunt ut laoreet</p></div></div>
    <div class="service-card"><svg width="38" height="38" viewBox="0 0 38 38"><path d="M5 14h28l-3 16H8z" fill="#221a78"/><path d="M13 14l6-9 6 9" fill="none" stroke="#221a78" stroke-width="2.5"/></svg><div><h3>Online Store Design<br>&amp; Management</h3><p>Lorem ipsum dolor sit amet, consectetuer adipiscing elit, sed diam nonummy nibh euismod tincidunt ut laoreet</p></div></div>
    <div class="service-card"><svg width="38" height="38" viewBox="0 0 38 38"><circle cx="16" cy="16" r="10" fill="none" stroke="#221a78" stroke-width="3"/><path d="M23 23l10 10" stroke="#221a78" stroke-width="4"/></svg><div><h3>Local<br>SEO Management</h3><p>Lorem ipsum dolor sit amet, consectetuer adipiscing elit, sed diam nonummy nibh euismod tincidunt ut laoreet</p></div></div>
    <div class="service-card"><svg width="38" height="38" viewBox="0 0 38 38"><circle cx="19" cy="19" r="7" fill="#221a78"/><circle cx="19" cy="19" r="14" fill="none" stroke="#221a78" stroke-width="3" stroke-dasharray="6 4"/></svg><div><h3>Search Engine<br>Optimization</h3><p>Lorem ipsum dolor sit amet, consectetuer adipiscing elit, sed diam nonummy nibh euismod tincidunt ut laoreet</p></div></div>
    <div class="service-card"><svg width="38" height="38" viewBox="0 0 38 38"><circle cx="10" cy="10" r="5" fill="#221a78"/><circle cx="28" cy="10" r="5" fill="#221a78"/><circle cx="19" cy="28" r="5" fill="#221a78"/><path d="M10 10l9 18 9-18z" fill="none" stroke="#221a78" stroke-width="2"/></svg><div><h3>Social Media<br>Marketing</h3><p>Lorem ipsum dolor sit amet, consectetuer adipiscing elit, sed diam nonummy nibh euismod tincidunt ut laoreet</p></div></div>
    <div class="service-card"><svg width="38" height="38" viewBox="0 0 38 38"><rect x="4" y="8" width="30" height="22" fill="none" stroke="#221a78" stroke-width="2.5"/><path d="M9 15h20M9 21h14" stroke="#221a78" stroke-width="2"/></svg><div><h3>Marketing<br>Material &amp; Print Design</h3><p>Lorem ipsum dolor sit amet, consectetuer adipiscing elit, sed diam nonummy nibh euismod tincidunt ut laoreet</p></div></div>
    <div class="service-card"><svg width="38" height="38" viewBox="0 0 38 38"><circle cx="19" cy="19" r="13" fill="none" stroke="#221a78" stroke-width="3"/><path d="M19 10v9l6 4" stroke="#221a78" stroke-width="3" fill="none"/></svg><div><h3>Outsourcing<br>Management</h3><p>Lorem ipsum dolor sit amet, consectetuer adipiscing elit, sed diam nonummy nibh euismod tincidunt ut laoreet</p></div></div>
    <div class="service-card"><svg width="38" height="38" viewBox="0 0 38 38"><circle cx="12" cy="12" r="5" fill="#221a78"/><circle cx="26" cy="12" r="5" fill="#221a78"/><path d="M3 30c0-6 4-10 9-10s9 4 9 10zM17 30c0-6 4-10 9-10s9 4 9 10z" fill="#221a78"/></svg><div><h3>Consulting<br>Service</h3><p>Lorem ipsum dolor sit amet, consectetuer adipiscing elit, sed diam nonummy nibh euismod tincidunt ut laoreet</p></div></div>
  </div>
</section>

<section class="cta" role="img" aria-label="Dark photo of a desk with a laptop behind the call to action">
  <p>Lorem ipsum dolor sit amet, consectetuer adipiscing elit, sed diam nonummy nibh euismod tincidunt ut laoreet dolore magna aliquam erat volutpat. Ut wisi enim ad minim veniam, quis nostrud exerci tation ullamcorper.</p>
  <span class="btn">CONTACT US NOW &#187;</span>
</section>

<section class="different">
  <h2 class="section-title">WHAT MAKES <b>ME DIFFERENT?</b></h2>
  <div class="features">
    <div class="feature"><div class="feature-icon"><svg width="40" height="40" viewBox="0 0 40 40"><path d="M20 5l16 29H4z" fill="none" stroke="#221a78" stroke-width="3"/><path d="M20 15v9M20 28v2" stroke="#221a78" stroke-width="3"/></svg></div><h4>100% Risk Free<br>Investment</h4><p>If we are unable to deliver anything that we say we can we will refund you 100% of your investment.</p></div>
    <div class="feature"><div class="feature-icon"><svg width="40" height="40" viewBox="0 0 40 40"><rect x="5" y="10" width="30" height="20" rx="3" fill="none" stroke="#221a78" stroke-width="3"/><path d="M5 17h30" stroke="#221a78" stroke-width="3"/></svg></div><h4>Customer Loyalty<br>Program</h4><p>After 12 months of on time payments, customers will receive cash back reward bonuses.</p></div>
    <div class="feature"><div class="feature-icon"><svg width="40" height="40" viewBox="0 0 40 40"><circle cx="20" cy="13" r="7" fill="#221a78"/><path d="M7 35c0-8 6-13 13-13s13 5 13 13z" fill="#221a78"/></svg></div><h4>Unmatched Personal<br>Service</h4><p>Do you need us to come to your office to help train staff on the management of your new site?</p></div>
    <div class="feature"><div class="feature-icon"><svg width="40" height="40" viewBox="0 0 40 40"><rect x="4" y="9" width="26" height="18" rx="3" fill="none" stroke="#221a78" stroke-width="3"/><circle cx="28" cy="26" r="8" fill="#221a78"/></svg></div><h4>Multiple Payment<br>Options Available</h4><p>Website Leasing, 90 Days Same As Cash, Website Financing</p></div>
  </div>
</section>

<section class="portfolio">
  <h2 class="section-title">WORK <b>PORTFOLIO</b></h2>
  <div class="filters"><span class="on">All</span><span>Website Design</span><span>Logo Design And Branding Materials</span><span>Local Seo Management</span></div>
  <div class="work-grid">
    <div class="work" role="img" aria-label="Website mockup with athlete photo" style="background:linear-gradient(180deg,#3b4456 0 14%,#f2f3f5 14% 100%),#f2f3f5;background:radial-gradient(ellipse 22% 40% at 65% 60%,#7d8696,rgba(125,134,150,0)),linear-gradient(180deg,#3b4456 0 14%,#eef0f3 14%)"></div>
    <div class="work" role="img" aria-label="Orange branding stationery set" style="background:radial-gradient(ellipse 30% 40% at 35% 45%,#f08a2a,rgba(240,138,42,0)),radial-gradient(ellipse 30% 35% at 70% 60%,#2d4a8a,rgba(45,74,138,0)),linear-gradient(135deg,#f7f3ee,#e5ddd3)"></div>
    <div class="work" role="img" aria-label="Logo sample on grey backdrop" style="background:radial-gradient(ellipse 28% 38% at 35% 45%,#c23a7a,rgba(194,58,122,0)),radial-gradient(circle at 65% 45%,#e0e0e0 0 10%,rgba(224,224,224,0) 11%),linear-gradient(135deg,#6a6a70,#3c3c42)"></div>
    <div class="work" role="img" aria-label="Teal local search illustration" style="background:radial-gradient(ellipse 30% 35% at 50% 55%,#f4f6f8,rgba(244,246,248,0)),radial-gradient(circle at 70% 30%,#e4473a 0 8%,rgba(228,71,58,0) 9%),linear-gradient(135deg,#2bb0c4,#1a7f94)"></div>
    <div class="work" role="img" aria-label="Colourful logo concept on white" style="background:radial-gradient(ellipse 25% 35% at 35% 45%,#f6b23a,rgba(246,178,58,0)),radial-gradient(ellipse 25% 35% at 65% 45%,#3a7be0,rgba(58,123,224,0)),#fbfbfb"></div>
    <div class="work" role="img" aria-label="Blue web workflow illustration" style="background:radial-gradient(ellipse 30% 30% at 50% 50%,#f5b43a,rgba(245,180,58,0)),linear-gradient(135deg,#3aa0e8,#1c6cc0)"></div>
    <div class="work" role="img" aria-label="Responsive website shown on devices" style="background:linear-gradient(180deg,#262a33 0 12%,rgba(0,0,0,0) 12%),radial-gradient(ellipse 40% 22% at 50% 35%,#d0532e,rgba(208,83,46,0)),linear-gradient(135deg,#f6f6f6,#dcdcdc)"></div>
    <div class="work" role="img" aria-label="Business card and letterhead mockup" style="background:radial-gradient(ellipse 22% 30% at 70% 55%,#23252b,rgba(35,37,43,0)),linear-gradient(135deg,#ffffff,#c9ccd2)"></div>
  </div>
</section>

<section class="team">
  <h2 class="section-title">OUR <b>TEAM</b></h2>
  <span class="arrow" style="left:98px"></span><span class="arrow" style="right:98px"></span>
  <div class="team-row">
    <div class="member active"><div class="photo" role="img" aria-label="Portrait of team member"></div><h4>Sam Porter</h4><p>Chief Executive Officer</p><div class="social"><i></i><i></i><i></i><i></i></div></div>
    <div class="member"><div class="photo" role="img" aria-label="Portrait of team member"></div><h4>Sam Porter</h4><p>Chief Operations Officer</p><div class="social"><i></i><i></i><i></i><i></i></div></div>
    <div class="member"><div class="photo" role="img" aria-label="Portrait of team member"></div><h4>Sam Porter</h4><p>Chief Technical Officer</p><div class="social"><i></i><i></i><i></i><i></i></div></div>
    <div class="member"><div class="photo" role="img" aria-label="Portrait of team member"></div><h4>Sam Porter</h4><p>Finance</p><div class="social"><i></i><i></i><i></i><i></i></div></div>
    <div class="member"><div class="photo" role="img" aria-label="Portrait of team member"></div><h4>Sam Porter</h4><p>Chief Executive Officer</p><div class="social"><i></i><i></i><i></i><i></i></div></div>
  </div>
  <div class="team-bio">
    <p>Lorem ipsum dolor sit amet, consectetuer adipiscing elit, sed diam nonummy nibh euismod tincidunt ut laoreet dolore magna aliquam erat volutpat. Ut wisi enim ad minim veniam, quis nostrud exerci tation ullamcorper suscipit lobortis nisl ut aliquip ex ea commodo consequat. Duis autem vel eum iriure dolor in hendrerit in vulputate velit esse molestie consequat, vel illum dolore eu feugiat nulla facilisis at vero eros et accumsan et iusto odio dignissim qui blandit praesent luptatum zzril delenit augue duis dolore te feugait nulla facilisi.</p>
    <p>Lorem ipsum dolor sit amet, consectetuer adipiscing elit, sed diam nonummy nibh euismod tincidunt ut laoreet dolore magna aliquam erat volutpat. Ut wisi enim ad minim veniam, quis nostrud exerci tation ullamcorper suscipit lobortis nisl ut aliquip ex ea commodo consequat. Duis autem vel eum iriure dolor in hendrerit in vulputate velit esse molestie consequat, vel illum dolore eu feugiat nulla facilisis at vero eros et accumsan et iusto odio dignissim qui blandit praesent luptatum zzril delenit augue duis dolore te feugait nulla facilisi.</p>
  </div>
</section>

<section class="reviews">
  <h2 class="section-title">CLIENT <b>REVIEWS</b></h2>
  <div class="review-row">
    <div class="review"><div class="review-person"><div class="photo" role="img" aria-label="Portrait of client"></div><h4>Lorem Ipsum</h4><div class="stars">&#9733;&#9733;&#9733;&#9733;&#9733;</div></div><p>"Lorem ipsum ut amet ca adipiscihasdiahl psul mo wark aliquer eostiuet ut te dolore ma aliquarem kam nibh enim non veni exercitation ullamco qui cillmol ameim con adipiscig ulmadim do eiusmod te quo uum accusa dolum enenque laudantium quis olist. Accusam dolorumque magnamnumquo laudantium godrw fumbo facilisi doloremque."</p></div>
    <div class="review"><div class="review-person"><div class="photo" role="img" aria-label="Portrait of client"></div><h4>Lorem Ipsum</h4><div class="stars">&#9733;&#9733;&#9733;&#9733;&#9733;</div></div><p>"Lorem ipsum ut amet ca adipiscihasdiahl psul mo wark aliquer eostiuet ut te dolore ma aliquarem kam nibh enim non veni exercitation ullamco qui cillmol ameim con adipiscig ulmadim do eiusmod te quo uum accusa dolum enenque laudantium quis olist. Accusam dolorumque magnamnumquo laudantium godrw fumbo facilisi doloremque."</p></div>
  </div>
  <div class="slider-line"><i></i></div>
</section>

<section class="clients">
  <h2 class="section-title">OUR <b>CLIENTS</b></h2>
  <span class="chev" style="left:98px">&#8249;</span><span class="chev" style="right:98px">&#8250;</span>
  <div class="client-row">
    <div class="client"><i></i>Northline</div>
    <div class="client">Kestrel</div>
    <div class="client"><i></i>Halvorsen</div>
    <div class="client"><i></i>Meridia</div>
    <div class="client">Oakform</div>
    <div class="client">Kestrel</div>
  </div>
</section>

<div class="newsletter">
  <svg width="28" height="28" viewBox="0 0 28 28"><rect x="2" y="6" width="24" height="16" fill="#fff"/><path d="M2 6l12 9 12-9" fill="none" stroke="#221a78" stroke-width="2"/></svg>
  <h3>SUBSCRIBE OUR NEWSLETTER</h3>
  <div class="field">Enter Email Address<span>SUBSCRIBE &#187;</span></div>
</div>

<footer class="site-footer">
  <div>
    <h4>QUICK LINKS</h4>
    <ul><li>&#8250; Home</li><li>&#8250; SERVICES &amp; PRICING</li><li>&#8250; OUR TEAM</li><li>&#8250; CLIENTS/PORTFOLIO</li><li>&#8250; Contact Us</li></ul>
  </div>
  <div style="width:200px">
    <h4>CONTACT DETAILS</h4>
    <div class="contact-line"><svg width="12" height="14" viewBox="0 0 12 14"><path d="M6 0a5 5 0 0 1 5 5c0 4-5 9-5 9S1 9 1 5a5 5 0 0 1 5-5z" fill="#fff"/></svg><span>BRIGHT HARBOR WEB DESIGN<br>0902 Lorem ipsum amet<br>ca adipiscihasdiahl</span></div>
    <div class="contact-line"><svg width="12" height="12" viewBox="0 0 12 12"><path d="M2 1l3 3-1.5 1.5c1 2 2 3 4 4L9 8l3 3-2 1C5 12 0 7 0 2z" fill="#fff"/></svg>123.456.7890</div>
    <div class="contact-line"><svg width="12" height="12" viewBox="0 0 12 12"><path d="M2 1l3 3-1.5 1.5c1 2 2 3 4 4L9 8l3 3-2 1C5 12 0 7 0 2z" fill="#fff"/></svg>123.456.7890</div>
    <div class="contact-line"><svg width="12" height="10" viewBox="0 0 12 10"><rect width="12" height="10" fill="#fff"/></svg>info@brightharbor.com</div>
  </div>
  <div class="inquiry">
    <h4>QUICK INQUIRY</h4>
    <div class="input">Name</div><div class="input">Email</div><div class="input msg">Message</div>
    <span class="btn-small">SUBMIT &#187;</span>
  </div>
  <div class="footer-brand">
    <div class="brand-name">BRIGHT HARBOR<small>WEB DESIGN</small></div>
    <div class="footer-social"><i></i><i></i><i></i><i style="background:#c0392b"></i></div>
  </div>
</footer>
<div class="copyright">Copyright &#169; 2017 BRIGHT HARBOR WEB DESIGN. All Rights Reserved.</div>

</body>
</html>
```